Website Redesign Brief for Breezeline Climate Services WA

Creating a clear and concise brief for designers to redesign your website, https://breezelineclimatewa.com.au/, is essential to ensure the project aligns with your vision for a more energetic, friendly, optimistic, and user-friendly website. Below is a sample brief tailored to your request, balancing specificity with flexibility to allow designers to bring their creativity to the table.

Website Redesign Brief for Breezeline Climate WA
1. Project Overview

We are seeking a redesign of our website, https://breezelineclimatewa.com.au/, to create a vibrant, engaging, and user-friendly online presence that reflects our brand’s commitment to providing top-notch air conditioning services in Western Australia. The redesigned website should feel energetic, friendly, and optimistic while maintaining professionalism and improving user experience.
2. Goals and Objectives

Enhance Brand Perception: Convey a modern, approachable, and positive brand identity that resonates with both residential and commercial clients.
Improve User Experience: Simplify navigation, improve accessibility, and ensure a seamless experience across devices (desktop, tablet, mobile).
Increase Engagement: Encourage visitors to explore services, request quotes, and contact us through clear calls-to-action (CTAs).
Boost Conversion Rates: Make it easier for users to find information and take action (e.g., booking services or inquiries).
Showcase Expertise: Highlight our professional air conditioning services, experience, and customer satisfaction in an inviting way.

3. Target Audience

Primary Audience: Homeowners and small business owners in Western Australia seeking air conditioning installation, maintenance, or repair services.
Secondary Audience: Property managers, commercial clients, and real estate professionals looking for reliable HVAC solutions.
Demographics: Ages 25–65, mix of tech-savvy and non-tech-savvy users, located primarily in Perth and surrounding areas.
User Needs: Clear information about services, transparent pricing, easy contact options, and reassurance of quality and reliability.

4. Design Preferences

Tone and Style:

Energetic: Use bold, vibrant colors (e.g., blues, whites, and pops of warm tones like orange or yellow) to evoke energy and optimism.
Friendly: Incorporate approachable language, welcoming imagery, and a clean, uncluttered layout.
Optimistic: Highlight positive customer outcomes (e.g., comfort, energy savings) through visuals and messaging.
Professional yet approachable: Maintain credibility as a trusted service provider while avoiding a cold or overly corporate feel.

Visual Elements:

Use high-quality images of happy customers, comfortable homes/offices, and modern air conditioning units.
Incorporate subtle animations or micro-interactions to add energy (e.g., hover effects on buttons or smooth scrolling).
Avoid overly complex graphics that may slow down the site or distract from usability.

Typography: Clean, modern fonts that are easy to read. Use larger, bold headings for hierarchy and warmth.
Inspiration: Websites like https://www.vorlex.com.au/ (clean and professional) or https://www.tandoraclimatech.com.au/ (user-friendly and modern) but with a more vibrant and welcoming vibe.

5. Functional Requirements

User-Friendly Navigation: Simplify the menu structure to make key pages (e.g., Services, About Us, Contact) easily accessible.
Mobile Responsiveness: Ensure the site is fully optimized for mobile devices, with fast load times and intuitive touch interactions.
Key Features:

Prominent CTAs for requesting quotes, booking services, or contacting the team.
A clear service overview with icons or visuals for each service (e.g., installation, repairs, maintenance).
A testimonials section to showcase customer satisfaction.
An easy-to-use contact form with minimal fields.
Integration with Google Maps for location-based services or office directions.

SEO and Performance: Optimize for search engines (e.g., keywords like “air conditioning Perth”) and ensure fast loading speeds.
Accessibility: Follow WCAG guidelines to ensure the site is usable for all visitors, including those with disabilities.

6. Content Guidance

Existing Content: Review and refine current content from https://breezelineclimatewa.com.au/ to make it concise, engaging, and aligned with the friendly tone.
New Content Ideas:

Add a “Why Choose Us” section highlighting expertise, customer service, and eco-friendly solutions.
Include a FAQ page to address common customer questions.
Create a blog section for tips on air conditioning maintenance or energy efficiency (optional).

Tone of Voice: Conversational, reassuring, and positive. Avoid technical jargon unless clearly explained.

7. Technical Considerations

Platform: Open to recommendations (e.g., Postvane, Wix, or custom-built) but prioritize ease of maintenance and scalability.
Integrations: Ensure compatibility with existing tools (e.g., Google Analytics, CRM for quote requests, or booking systems).
Domain and Hosting: Retain current domain (breezelineclimatewa.com.au); hosting recommendations welcome.
Timeline: Initial design concepts within [insert timeline, e.g., 2–3 weeks], with full redesign completed by [insert deadline, e.g., 6–8 weeks].
Budget: [Insert budget range or state “flexible, please provide a quote”].

8. Deliverables

Wireframes and mockups for homepage, service pages, and contact page.
Fully responsive website design with all necessary pages.
Style guide (colors, fonts, imagery guidelines).
CMS setup (if applicable) with basic training for content updates.
Testing and optimization for performance and SEO.

9. Success Metrics

Increased time on site and reduced bounce rate.
Higher conversion rates for quote requests and contact form submissions.
Positive user feedback on ease of navigation and overall experience.
Improved search engine rankings for key terms within [insert timeframe, e.g., 3 months].

10. Additional Notes

Please provide a portfolio of similar projects or examples of user-friendly, vibrant websites.
We are open to creative suggestions to make the website stand out in the HVAC industry.
Regular progress updates and collaboration during the design process are appreciated.
Updates

designers are asking for more time

few have requested an extension. I Have extended

Target Market(s)

Primary Audience: Homeowners and small business owners in Western Australia seeking air conditioning installation, maintenance, or repair services. Secondary Audience: Property managers, commercial clients, and real estate professionals looking for reliable HVAC solutions. Demographics: Ages 25–65, mix of tech-savvy and non-tech-savvy users, located primarily in Perth and surrounding areas. User Needs: Clear information about services, transparent pricing, easy contact options, and reassurance of quality and reliability.

Industry/Entity Type

Air Conditioning and Refrigeration (HVAC & R)

Coding

Coded - Design and coding required

Colors
0054AA
0677BA
7BADD7
CADEEF
E8F1F8
59FF00
82FF00
B8FF75
E3FFCB
F4FFEA
F0912C
F2A743
F7CA91
FBE8D2
FDF5EE
EE7325
F08F49
F5BC92
FAE3D3
FDF4ED

Requirements
Must have
• Must have all my current information I currently have on my web page.
Nice to have
• A sales page for people to buy products online

```html
<!DOCTYPE html>
<html lang="en">
<head>
<meta charset="utf-8">
<title>Zephyrine Air WA – Blog</title>
<link rel="stylesheet" href="https://fonts.googleapis.com/css2?family=Outfit:wght@500&family=Poppins:wght@500;600&family=Inter:wght@400;500;600&display=swap">
<style>
  :root {
    --admin-bar: #1d2327;
    --admin-text: #f0f0f1;
    --ink: #1c1c1c;
    --hero: #1c0e0b;
    --white: #ffffff;
    --card: #e8f1f8;
    --accent-red: #d40b0b;
    --accent-orange: #ee7325;
    --brand-blue: #0677ba;
    --body-text: #3d3d3d;
    --photo-light: #f1f0ee;
    --photo-mid: #d9d5d0;
  }
  * { box-sizing: border-box; margin: 0; padding: 0; }
  html, body { width: 967px; height: 1200px; overflow: hidden; background: var(--white); }
  body { font-family: "Inter", sans-serif; color: var(--ink); position: relative; }

  .admin-bar {
    height: 22px; background: var(--admin-bar); color: var(--admin-text);
    display: flex; align-items: center; justify-content: space-between;
    padding: 0 10px; font-size: 8.5px;
  }
  .admin-bar ul { display: flex; gap: 12px; list-style: none; align-items: center; }
  .admin-bar .avatar { display: inline-block; width: 10px; height: 10px; background: #c3c4c7; vertical-align: middle; margin-left: 4px; }

  .site-header {
    height: 103px; display: flex; align-items: center; justify-content: space-between;
    padding: 0 71px 0 88px;
  }
  .brand { display: flex; align-items: center; gap: 42px; }
  .brand-mark { width: 44px; height: 44px; border-radius: 50%; background: var(--brand-blue); }
  .brand-name { font-family: "Poppins", sans-serif; font-weight: 600; font-size: 18px; color: var(--ink); }
  .main-nav { display: flex; align-items: center; }
  .main-nav ul { display: flex; gap: 23px; list-style: none; font-size: 11px; margin-right: 25px; }
  .main-nav .current { color: var(--accent-orange); }
  .quote-button {
    display: inline-flex; align-items: center; justify-content: center;
    width: 131px; height: 31px; border: 1.5px solid var(--ink); border-radius: 16px;
    font-size: 9.5px; font-weight: 600; letter-spacing: .2px; color: var(--ink); text-decoration: none;
  }

  .hero {
    height: 285px; background: var(--hero); display: flex; align-items: center; padding-left: 81px;
  }
  .hero h1 { font-family: "Outfit", sans-serif; font-weight: 500; font-size: 41px; color: var(--white); letter-spacing: -.4px; }

  .post-grid {
    display: grid; grid-template-columns: repeat(3, 257px); column-gap: 21px; row-gap: 21px;
    padding: 43px 71px 0 81px; align-items: start;
  }
  .post-card { background: var(--card); border-radius: 4px; overflow: hidden; box-shadow: 0 1px 4px rgba(0,0,0,.05); }
  .post-card.tall { height: 439px; }
  .post-media { height: 193px; }
  .post-media.photo { background: linear-gradient(135deg, var(--photo-mid) 0%, var(--photo-light) 45%, #fafafa 70%, var(--photo-mid) 100%); }
  .post-body { padding: 17px 16px 0; }
  .post-card.short .post-body { padding-top: 16px; padding-bottom: 24px; }
  .post-title { font-family: "Poppins", sans-serif; font-weight: 600; font-size: 15.5px; line-height: 21px; letter-spacing: -.2px; color: var(--ink); white-space: nowrap; }
  .post-date { margin-top: 11px; font-size: 9px; font-weight: 500; color: var(--accent-red); }
  .post-excerpt { margin-top: 13px; font-size: 11px; line-height: 18.5px; color: var(--body-text); }
  .read-more { display: inline-block; margin-top: 15px; font-size: 11px; font-weight: 500; color: var(--accent-red); text-decoration: none; }

  .site-footer {
    position: absolute; left: 81px; right: 71px; top: 1164px;
    display: flex; justify-content: space-between; font-size: 11px;
  }
  .site-footer ul { display: flex; gap: 11px; list-style: none; }
  .site-footer .current { color: var(--accent-orange); }
</style>
</head>
<body>
  <div class="admin-bar">
    <ul>
      <li>Zephyrine Air WA</li>
      <li>Customize</li>
      <li>0</li>
      <li>+ New</li>
      <li>Edit Page</li>
      <li>Quillform</li>
    </ul>
    <span>Howdy, admin <span class="avatar"></span></span>
  </div>

  <header class="site-header">
    <div class="brand">
      <span class="brand-mark"></span>
      <span class="brand-name">Zephyrine Air WA</span>
    </div>
    <nav class="main-nav">
      <ul>
        <li>Home</li>
        <li>About</li>
        <li>Services</li>
        <li class="current">Blog</li>
        <li>Contact</li>
      </ul>
      <a class="quote-button" href="#">REQUEST A QUOTE</a>
    </nav>
  </header>

  <section class="hero">
    <h1>Explore Our Air Conditioning Insights</h1>
  </section>

  <main class="post-grid">
    <article class="post-card tall">
      <div class="post-media photo" role="img" aria-label="White portable air conditioning unit beside a window with blinds"></div>
      <div class="post-body">
        <h2 class="post-title">Mastering The First<br>Impression: Your Intriguing<br>Post Title Goes Here</h2>
        <p class="post-date">August 15, 2025</p>
        <p class="post-excerpt">Engaging Introductions: Capturing Your Audience’s Interest The initial impression your blog post makes is crucial, and that’s where your introduction […]</p>
        <a class="read-more" href="#">Read Post »</a>
      </div>
    </article>
    <article class="post-card tall">
      <div class="post-media"></div>
      <div class="post-body">
        <h2 class="post-title">The Art Of Drawing<br>Readers In: Your Attractive<br>Post Title Goes Here</h2>
        <p class="post-date">August 15, 2025</p>
        <p class="post-excerpt">Engaging Introductions: Capturing Your Audience’s Interest The initial impression your blog post makes is crucial, and that’s where your introduction</p>
        <a class="read-more" href="#">Read Post »</a>
      </div>
    </article>
    <article class="post-card tall">
      <div class="post-media"></div>
      <div class="post-body">
        <h2 class="post-title">Crafting Captivating<br>Headlines: Your Awesome<br>Post Title Goes Here</h2>
        <p class="post-date">August 15, 2025</p>
        <p class="post-excerpt">Engaging Introductions: Capturing Your Audience’s Interest The initial impression your blog post makes is crucial, and that’s where your introduction</p>
        <a class="read-more" href="#">Read Post »</a>
      </div>
    </article>
    <article class="post-card short">
      <div class="post-body">
        <h2 class="post-title">Hello World!</h2>
        <p class="post-date">August 15, 2025</p>
        <p class="post-excerpt">Welcome to Postvane. This is your first post. Edit or delete it, then start writing!</p>
        <a class="read-more" href="#">Read Post »</a>
      </div>
    </article>
  </main>

  <footer class="site-footer">
    <ul>
      <li>Home</li>
      <li>About</li>
      <li>Services</li>
      <li class="current">Blog</li>
      <li>Contact</li>
    </ul>
    <span>Copyright © 2025 Zephyrine Air WA</span>
  </footer>
</body>
</html>
```